New, modern business card for growing audiology practice

We need a new business card for our audiology practice. Our logo and website have recently changed (more modern) and we want our business cards to reflect this change.
We conduct hearing tests, perform earwax removals, and fit & dispense hearing aids to our patients. We are a family owned practice in which the owner is the one who works directly with the patient. I have attached logos in various formats to use, as well as two ideas I found on this website; as well as a scanned copy of our current logo. Good luck!

Industry/Entity Type

Business

Contact Information for Business Card

Company name: Tolvera Hearing Center
Provider name: Peter Wolstenby, Au.D. F/NSB
Phone number: (440) 683-5127
Address: 837 W. Lindell Ave. Alder Falls, OH 44871
email: tolverahearing@postvane.com
website: tolverahearing.com

Colors
000000
aaaaaa
dbdbdb
cacaca
9bcb3c
afd23c
cadf82
b1b1b1

Requirements
Must have
• My card must include information in the "details" section. In the attached images, I found a few that I liked and I would like to model after - "brisky bouncin'" and "Sound Method Center".
• Must be horizontal.
• Must include logos provided. I uploaded them in various file formats and various ways.
• Must match logo font, if possible, if not, please get as close as you can.
Nice to have
• I really like the idea of having a color on one side with just the logo and company name and the contact information and provider name on the other side. I also really like the idea of having the main color dominating on the logo/company side with accent of that same color on the contact side of the card.
Should not have
• Must not be vertical.

```html
<!DOCTYPE html>
<html lang="en">
<head>
<meta charset="utf-8">
<title>Tolvera Hearing Center – Business Card</title>
<link rel="stylesheet" href="https://fonts.googleapis.com/css2?family=Source+Sans+3:wght@400;600&display=swap">
<style>
  :root {
    --backdrop: #000000;
    --card: #333438;
    --ink: #f2f2f2;
    --green: #7fae3e;
    --rule: #46474c;
  }
  * { margin: 0; padding: 0; box-sizing: border-box; }
  html, body {
    width: 1200px; height: 900px; overflow: hidden;
    background: var(--backdrop);
    font-family: "Source Sans 3", "Helvetica Neue", Arial, sans-serif;
    color: var(--ink);
  }
  .canvas { position: relative; width: 1200px; height: 900px; }
  .card {
    position: absolute; top: 271px;
    width: 457px; height: 281px;
    background: var(--card);
    border-radius: 14px;
  }
  .card--contact { left: 137px; }
  .card--brand { left: 626px; }

  .brand-block {
    position: absolute; left: 40px; top: 78px; width: 150px;
    color: var(--green); font-weight: 600;
    font-size: 21px; line-height: 1.2; letter-spacing: 0.04em;
    text-transform: uppercase;
  }
  .divider {
    position: absolute; left: 196px; top: 79px;
    width: 1px; height: 132px; background: var(--rule);
  }
  .details { position: absolute; left: 221px; top: 77px; }
  .provider { font-size: 17px; font-weight: 600; white-space: nowrap; }
  .provider .surname { color: var(--green); }
  .provider .credentials { font-size: 12.5px; }
  .address { margin-top: 12px; font-size: 13px; line-height: 19px; }
  .contact-list { margin-top: 14px; list-style: none; font-size: 13px; line-height: 19px; }
  .contact-list li { display: flex; align-items: center; gap: 8px; }
  .contact-list svg { width: 10px; height: 10px; fill: var(--green); flex: none; }

  .wordmark {
    position: absolute; left: 57px; top: 124px;
    display: flex; align-items: center; gap: 12px;
    font-size: 25px; font-weight: 400; letter-spacing: 0.01em;
    text-transform: uppercase; color: var(--ink); white-space: nowrap;
  }
  .wordmark .dot {
    width: 14px; height: 14px; border-radius: 50%; background: var(--green);
  }
</style>
</head>
<body>
<main class="canvas">
  <section class="card card--contact">
    <div class="brand-block">Tolvera<br>Hearing<br>Center</div>
    <div class="divider"></div>
    <div class="details">
      <p class="provider">Peter <span class="surname">Wolstenby</span>, <span class="credentials">Au.D. F/NSB</span></p>
      <p class="address">837 W. Lindell Ave.<br>Alder Falls, OH 44871</p>
      <ul class="contact-list">
        <li>
          <svg viewBox="0 0 10 10" aria-hidden="true"><path d="M2 0.5 L3.6 2.6 L2.7 3.6 Q3.8 5.9 6.3 7.3 L7.4 6.4 L9.5 8 L8.4 9.5 Q3.5 9 0.5 1.6 Z"/></svg>
          (440) 683-5127
        </li>
        <li>
          <svg viewBox="0 0 10 10" aria-hidden="true"><path d="M0.5 2 H9.5 V8 H0.5 Z M1.2 2.6 L5 5.4 L8.8 2.6" stroke="#333438" stroke-width="0.8"/></svg>
          tolverahearing@postvane.com
        </li>
        <li>
          <svg viewBox="0 0 10 10" aria-hidden="true"><circle cx="5" cy="5" r="4.6"/><path d="M0.6 5 H9.4 M5 0.5 Q2.6 5 5 9.5 M5 0.5 Q7.4 5 5 9.5" stroke="#333438" stroke-width="0.7" fill="none"/></svg>
          tolverahearing.com
        </li>
      </ul>
    </div>
  </section>

  <section class="card card--brand">
    <div class="wordmark"><span class="dot"></span>Tolvera Hearing Center</div>
  </section>
</main>
</body>
</html>
```